Blood Testing Health App

We are looking for a graphics designer to create a web app for us so that we may insert it into a health management website system.
For branding purposes we are at www.Vantiqor.com and we are revamping our website... Example of new colors attached.
How we work...
We are a blood testing company based in the USA.
We offer a blood testing service nationwide in the USA.
We allow customers to order tests directly from us, visit a lab, have their blood drawn, or submit a urine sample, the lab tests it and they send the results back to our computer system and we share it with the customer.
The benefits of this are the customer does not need to go to the doctor and pay for the doctors visit to order these tests, which save them money. The tests are cheaper than going through the doctor. The customer simply uses us to get the test and the results and they can then take the results to their doctor... this process has saved them money. Others may be interested in regular check ups for blood work etc... and this allows them to do it with out needing a doctor, or if you have no insurance, this is a cheaper option too. We are quicker than a doctor, customers do not need appointments etc.
Hopefully you now have a better understanding as to what we do.
Here is the spec.
The app screen size is 750 px wide by 700 px high. ( A pdf is attached to show where the app is going to go, it is on page 3 of the pdf) The customer will have the ability to scroll… therefore the length of the page can be longer.
The app will consist of the following sections
Entry Page –
This will be the first page the user sees upon opening the app. This will be where they are directed from to the sections of the app discussed below. This needs to be branded for VantiQor with a modern look.
1 – Order Test (Giving them the ability to purchase a blood test within the app)
2 – VantiQor Dashboard (A dashboard that has everything they could need to use our service_
How it works Section on entry page – this will be a simple set of graphics showing how the service works. We already have the graphics for this, they do not need to be built again. They are attached to this brief
Basic structure of sections –
Order Test –
This page contains all tests, filed in categories – and Sub categories – Each test needs a link to an Information section – Price – Buy Now – Cart Process
VantiQor Dashboard –
A page of icons along the top of the app
- My Confirmation
- My Nearest Lab
- My Receipt
- My Orders
- My Account
- My Results
- My Inbox
- Contact Us
Sections in more detail -
Order A Test –
Show all categories/ sub categories – There are 23 categories, 14 sub categories, and within these categories are 300 tests - Here is the information for the categories etc - http://www.vantiqor.com/panels.aspx?PanelGroupID=4 Just in case it helps :)
We need to present this in a graphic format that is spacious, modern (brimlake, kivvo web appearance is the direction we are going for) We need it to be clear and not overwhelming to the customer.
Functionality idea…
Customer clicks category/ subcategory and tests appear.
Customer sees small 35 word description. For more information the test opens into a lightbox or expand the container which ever graphic designer believes to be most visually appealing
Buy Now must always be visible, along with price of the test
Buying process explained – Customer clicks buy now –
They are then taken to a Review Order screen ( This contains Order summary and choose payment method – insert payment details )
– Confirm payment –
Confirmation screen appears, thanking them.
They are then taken to the VantiQor Dashboard...
VantiQor Dashboard –
"My Confirmation" - Print Confirmation Order (PDF is in brief, we want this web based not a pdf download)
"My Nearest Lab Location" - This does not need to be designed because the web developer has this part under control, but we do need the icon in the dashboard
"My Receipt" - Print receipt - This does not exist in our system yet. So we need to create this from scratch - It will need to have - The test they are purchasing and the amount of the test - The customers name - The order ID - Must provide printer friendly option too
"My Orders" - This will have a list of orders - At the end of each order will be a status update of either "Test results" "Open order"
A graphic table format would be perfect. This will be linked to relevant results if they have been received. I have also attached a version of what the customer currently sees on our website. We know it is nasty ;) We are redesigning... but the information is there for this section to help design it with the right info. If the results are ready it will say in this list.
"Results Ready" will be a link to show those results once the customer has clicked the link, and the results will appear in the app, under the icons. There must be a printer friendly version too.
"My Results" Developer will sort this page out but we need the icon... It will be exactly like my orders but only show test results
"My Account" - This will be a place for them to update their personal information - Name, DOB, Address, Email Address
"My Inbox" - An inbox interface - Our way of contacting the customer for promotions we are running etc – We need a design of how this screen will appear. We also need the icon in the dashboard to have a notification on it if there are messages in the customers inbox. A little red 1, or circle with number of messages in the inbox.
"Customer Service" - This does not need to be designed because the web developer has this part under control, but we do need the icon in the dashboard
Icons appear along the top of app ( example - Mac icons/ iphone app icons) When the customer clicks an icon the content always appears below the icons
Here is more information for the icons and what should appear when each icon is clicked.
Screens to be designed –
Entry Page
Order A Test Page
Review Order Screen/Payment Screen - Show a lightbox that shows payment has been confirmed. Customer clicks close and are on the Confirmation Screen
VantiQor Dashboard - Screens mentioned in detail above
We can't wait to see your designs!
Please email any questions.
Hi all this is the first time we have used pixel harbor and understand the budget was too low for this project. We have now increased the budget to $2,000 and extended the deadline by another week
Hi all we are receiving some really great designs. I just added an example of the space that the web app will be going into... It is called "morvelapp.pdf"
Hi guys updated the brief. Hopefully this will help with the dashboard part of the design

```html
<!DOCTYPE html>
<html lang="en">
<head>
<meta charset="utf-8">
<title>VantiQor – Order A Test</title>
<link rel="stylesheet" href="https://fonts.googleapis.com/css2?family=Open+Sans:wght@400;600&display=swap">
<style>
  :root {
    --olive: #8a9a1c;
    --olive-soft: #a9b648;
    --cream: #f6f4da;
    --cream-strong: #f8f5cf;
    --ink: #2b2b2b;
    --muted: #6c6c6c;
    --brown: #3a2716;
    --white: #ffffff;
    --line: #c9cf8c;
    --grey-line: #c8c8c8;
  }
  * { box-sizing: border-box; margin: 0; padding: 0; }
  html, body { width: 692px; height: 1200px; overflow: hidden; }
  body {
    font-family: "Open Sans", sans-serif;
    background: var(--white);
    color: var(--ink);
    position: relative;
  }
  .app-header {
    height: 124px;
    background: linear-gradient(to bottom, var(--olive-soft) 0, var(--olive) 100%);
    display: flex;
    justify-content: center;
  }
  .brand {
    background: var(--white);
    width: 320px;
    display: flex;
    align-items: center;
    justify-content: center;
  }
  .brand-name {
    font-size: 40px;
    font-weight: 600;
    color: var(--ink);
  }
  .category-label {
    margin-top: 44px;
    text-align: center;
    color: var(--olive);
    font-size: 22px;
  }
  .category-select {
    margin: 12px 42px 0;
    height: 62px;
    border: 2px solid var(--grey-line);
    display: flex;
    align-items: center;
    justify-content: space-between;
    padding-left: 16px;
    background: var(--white);
  }
  .category-select span { font-size: 29px; color: var(--muted); }
  .select-arrow {
    width: 60px; height: 58px;
    border-left: 2px solid var(--grey-line);
    display: flex; align-items: center; justify-content: center;
    background: #f2f2f2;
  }
  .panel-heading {
    margin: 20px 54px 0;
    height: 52px;
    background: var(--cream-strong);
    border: 1px solid var(--line);
    border-bottom: none;
    text-align: center;
    font-size: 27px;
    line-height: 50px;
  }
  .panel-list {
    margin: 0 23px;
    border: 2px solid var(--olive-soft);
    border-bottom: none;
    padding: 6px 10px 0;
    height: 830px;
    overflow: hidden;
    list-style: none;
  }
  .panel-row {
    display: flex;
    align-items: center;
    min-height: 44px;
    margin-bottom: 3px;
    padding: 2px 8px;
    font-size: 20px;
  }
  .panel-row:nth-child(even) { background: var(--cream); }
  .panel-row.tall { min-height: 64px; }
  .panel-name { flex: 1; line-height: 1.3; padding-right: 6px; }
  .panel-row.single-line .panel-name { white-space: nowrap; }
  .panel-price { width: 88px; text-align: right; margin-right: 10px; }
  .add-to-cart {
    width: 118px; height: 30px;
    background: var(--olive);
    color: var(--white);
    border: none;
    font-family: inherit;
    font-size: 16px;
    font-weight: 600;
  }
  .app-footer {
    position: absolute;
    left: 0; right: 0; bottom: 0;
    height: 35px;
    background: var(--brown);
  }
</style>
</head>
<body>
  <header class="app-header">
    <div class="brand">
      <span class="brand-name">VantiQor</span>
    </div>
  </header>

  <p class="category-label">Select A Category</p>
  <div class="category-select">
    <span>Women's Health</span>
    <div class="select-arrow">
      <svg width="26" height="16" viewBox="0 0 26 16"><path d="M2 2 L13 13 L24 2" fill="none" stroke="#666" stroke-width="4"/></svg>
    </div>
  </div>

  <div class="panel-heading">Panel Name</div>
  <ul class="panel-list">
    <li class="panel-row"><span class="panel-name">Amenorrhea Profile</span><span class="panel-price">$105.00</span><button class="add-to-cart">Add to Cart</button></li>
    <li class="panel-row"><span class="panel-name">CA-125</span><span class="panel-price">$65.00</span><button class="add-to-cart">Add to Cart</button></li>
    <li class="panel-row"><span class="panel-name">Calcium, Ionized, Serum</span><span class="panel-price">$126.00</span><button class="add-to-cart">Add to Cart</button></li>
    <li class="panel-row"><span class="panel-name">Calcium, Serum</span><span class="panel-price">$45.00</span><button class="add-to-cart">Add to Cart</button></li>
    <li class="panel-row"><span class="panel-name">Candida Antibodies, Qualitative</span><span class="panel-price">$175.00</span><button class="add-to-cart">Add to Cart</button></li>
    <li class="panel-row tall"><span class="panel-name">Comprehensive Female Sexual<br>Health and Wellness</span><span class="panel-price">$455.00</span><button class="add-to-cart">Add to Cart</button></li>
    <li class="panel-row single-line"><span class="panel-name">Comprehensive Healthy Heart Profile</span><span class="panel-price">$249.00</span><button class="add-to-cart">Add to Cart</button></li>
    <li class="panel-row tall"><span class="panel-name">Comprehensive Metabolic Panel<br>(CMP 14)</span><span class="panel-price">$45.00</span><button class="add-to-cart">Add to Cart</button></li>
    <li class="panel-row tall"><span class="panel-name">Female Age Management<br>Follow-up Evaluaton</span><span class="panel-price">$460.00</span><button class="add-to-cart">Add to Cart</button></li>
    <li class="panel-row tall"><span class="panel-name">Female Age Management Initial<br>Evaluation</span><span class="panel-price">$640.00</span><button class="add-to-cart">Add to Cart</button></li>
    <li class="panel-row"><span class="panel-name">Female Cancer Screening</span><span class="panel-price">$270.00</span><button class="add-to-cart">Add to Cart</button></li>
    <li class="panel-row"><span class="panel-name">Female Ultimate Anti-Aging</span><span class="panel-price">$600.00</span><button class="add-to-cart">Add to Cart</button></li>
    <li class="panel-row"><span class="panel-name">Fibrinogen Activity</span><span class="panel-price">$59.80</span><button class="add-to-cart">Add to Cart</button></li>
    <li class="panel-row"><span class="panel-name">Candida Antibodies, Qualitative</span><span class="panel-price">$175.00</span><button class="add-to-cart">Add to Cart</button></li>
    <li class="panel-row"><span class="panel-name">Calcium, Serum</span><span class="panel-price">$45.00</span><button class="add-to-cart">Add to Cart</button></li>
  </ul>

  <footer class="app-footer"></footer>
</body>
</html>
```